Web Developer Needs a Business Card Design

I need a personal business card design that represents me as a web developer for potential employers. I would like the background to be a dark color on the front for contrast with my logo and name. The back will have all my information along with a smaller version of the logo. I want something with a modern look and feel, not too conservative. This will be used for potential employers and freelance work.

Industry/Entity Type

Business

Contact Information for Business Card

Front should have my logo and name. The back should have all my personal information which would include: name: Tom Varulek, phone: 570-614-3098, email: tomvarulek@quillbox.net, website url: www.tomvarulek.net, logo, web developer.

Font styles to use
Sans Serif

Requirements
Must have
• Must include my logo. The color palette base color will be the logo color.

```html
<!DOCTYPE html>
<html lang="en">
<head>
<meta charset="utf-8">
<title>Tom Varulek – Business Card</title>
<link rel="stylesheet" href="https://fonts.googleapis.com/css2?family=Open+Sans:wght@400;600&display=swap">
<style>
  :root {
    --ink: #0b0f0e;
    --mint: #7fd3c4;
    --paper: #f7f7f5;
    --stage: #e6e4df;
    --text-dark: #1b1d1c;
  }
  * { box-sizing: border-box; margin: 0; padding: 0; }
  html, body { width: 1200px; height: 902px; overflow: hidden; }
  body {
    background: var(--stage);
    font-family: "Open Sans", Arial, sans-serif;
    position: relative;
  }
  .card {
    position: absolute;
    width: 620px;
    height: 354px;
    background: var(--paper);
    box-shadow: 0 10px 24px rgba(0,0,0,.22);
    overflow: hidden;
  }
  .card-front { left: 50px; top: 60px; }
  .card-back { left: 530px; top: 488px; }
  .card-shapes { position: absolute; inset: 0; width: 100%; height: 100%; }

  .front-name {
    position: absolute;
    left: 28px; top: 50px;
    color: var(--mint);
    font-size: 30px;
    font-weight: 400;
    letter-spacing: .3px;
  }
  .brand-mark {
    position: absolute;
    display: flex;
    align-items: center;
    gap: 10px;
    color: var(--mint);
    font-weight: 600;
  }
  .brand-mark .ring {
    border: 4px solid var(--mint);
    border-radius: 50%;
  }
  .card-front .brand-mark { left: 238px; top: 168px; font-size: 26px; }
  .card-front .brand-mark .ring { width: 34px; height: 34px; }
  .card-back .brand-mark { left: 44px; top: 178px; font-size: 22px; }
  .card-back .brand-mark .ring { width: 28px; height: 28px; }

  .back-identity { position: absolute; left: 330px; top: 100px; color: var(--text-dark); }
  .back-identity .name { font-size: 32px; font-weight: 400; line-height: 1.05; }
  .back-identity .role { font-size: 17px; margin-left: 34px; color: #333; }

  .contact-list { position: absolute; left: 372px; top: 176px; list-style: none; }
  .contact-list li {
    display: flex; align-items: center; gap: 12px;
    font-size: 17px; color: var(--text-dark);
    height: 28px;
  }
  .contact-list svg { width: 16px; height: 16px; flex: none; }
</style>
</head>
<body>

<section class="card card-front" aria-label="Business card front">
  <svg class="card-shapes" viewBox="0 0 620 354" aria-hidden="true">
    <polygon points="0,0 620,0 620,66 300,66 282,100 0,100" fill="var(--ink)"/>
    <polyline points="0,108 287,108 305,74 620,74" fill="none" stroke="var(--mint)" stroke-width="5"/>
    <line x1="0" y1="272" x2="620" y2="272" stroke="var(--mint)" stroke-width="5"/>
    <rect x="0" y="279" width="620" height="75" fill="var(--ink)"/>
  </svg>
  <div class="front-name">Tom Varulek</div>
  <div class="brand-mark"><span class="ring"></span><span>Varulek</span></div>
</section>

<section class="card card-back" aria-label="Business card back">
  <svg class="card-shapes" viewBox="0 0 620 354" aria-hidden="true">
    <polygon points="0,0 620,0 620,52 330,52 312,90 0,90" fill="var(--ink)"/>
    <polyline points="0,98 317,98 335,60 620,60" fill="none" stroke="var(--mint)" stroke-width="5"/>
    <line x1="0" y1="286" x2="620" y2="286" stroke="var(--mint)" stroke-width="5"/>
    <rect x="0" y="293" width="620" height="61" fill="var(--ink)"/>
  </svg>
  <div class="brand-mark"><span class="ring"></span><span>Varulek</span></div>
  <div class="back-identity">
    <div class="name">Tom Varulek</div>
    <div class="role">web developer</div>
  </div>
  <ul class="contact-list">
    <li>
      <svg viewBox="0 0 16 16" aria-hidden="true"><rect width="16" height="16" fill="var(--mint)"/><path d="M5 3.5l2 2-1 1.2c.6 1.3 1.6 2.3 2.9 2.9l1.1-1 2 2-1.2 1.6C7.7 12 4 8.3 3.4 5z" fill="#fff"/></svg>
      570-614-3098
    </li>
    <li>
      <svg viewBox="0 0 16 16" aria-hidden="true"><rect width="16" height="16" fill="var(--mint)"/><circle cx="8" cy="8" r="4.5" fill="none" stroke="#fff" stroke-width="1.3"/><line x1="3.5" y1="8" x2="12.5" y2="8" stroke="#fff" stroke-width="1.1"/><ellipse cx="8" cy="8" rx="2" ry="4.5" fill="none" stroke="#fff" stroke-width="1.1"/></svg>
      www.tomvarulek.net
    </li>
    <li>
      <svg viewBox="0 0 16 16" aria-hidden="true"><rect width="16" height="16" fill="var(--mint)"/><rect x="3" y="4.5" width="10" height="7" fill="none" stroke="#fff" stroke-width="1.2"/><polyline points="3,4.8 8,8.6 13,4.8" fill="none" stroke="#fff" stroke-width="1.2"/></svg>
      tomvarulek@quillbox.net
    </li>
  </ul>
</section>

</body>
</html>
```